Lentil and Vegetable Soup (Sambar) Product Label Design

Sambar is the product and we need a label for that. The label size is 4"x3.33". Attached is the sample label containing all the necessary info.
Mainly show the images of the coconut, onions, chayotes, big egg plant and the lentils (Toor dal). Various design choices are encouraged. This includes various types of fonts, colors, backgrounds, etc.

```html
<!DOCTYPE html>
<html lang="en">
<head>
<meta charset="utf-8">
<title>Sambar Label</title>
<link rel="stylesheet" href="https://fonts.googleapis.com/css2?family=Lobster&family=Oswald:wght@600;700&family=Lora:ital,wght@1,600&family=Roboto+Condensed:wght@400;700&display=swap">
<style>
  :root {
    --page: #e9eaec;
    --label-yellow: #f6e81c;
    --label-cream: #fbf6c8;
    --brand-red: #d3202a;
    --tag-text: #fde27a;
    --ink: #3a2a12;
    --title-brown: #5a2a0c;
    --band-green: #2f7a36;
    --cup-white: #f7f7f7;
  }
  * { box-sizing: border-box; margin: 0; padding: 0; }
  html, body { width: 831px; height: 1200px; overflow: hidden; background: var(--page); }
  .label {
    position: absolute; left: 60px; top: 110px; width: 711px; height: 980px;
    background: var(--label-yellow);
    overflow: hidden;
  }
  .brand-band {
    position: absolute; left: 0; top: 0; width: 100%; height: 190px;
    background: linear-gradient(180deg, var(--cup-white) 0%, var(--label-cream) 100%);
    border-bottom: 6px solid var(--brand-red);
  }
  .brand-band::before {
    content: ""; position: absolute; left: 0; right: 0; top: 14px; height: 4px; background: var(--brand-red);
  }
  .brand-name {
    position: absolute; left: 0; right: 0; top: 52px; text-align: center;
    font-family: "Lobster", cursive; font-size: 104px; line-height: 1; color: var(--brand-red);
  }
  .side-copy {
    position: absolute; top: 210px;
    font-family: "Roboto Condensed", sans-serif; color: var(--ink);
  }
  .side-copy.ingredients { left: 18px; width: 128px; font-size: 13px; line-height: 1.5; }
  .side-copy.usage { right: 14px; width: 130px; font-weight: 700; font-size: 17px; line-height: 1.4; text-align: right; }
  .product-title {
    position: absolute; left: 0; right: 0; top: 250px; text-align: center;
    font-family: "Oswald", sans-serif; font-weight: 700; font-size: 64px; line-height: 1.3; letter-spacing: 2px;
    color: var(--title-brown);
  }
  .product-variant {
    position: absolute; left: 0; right: 0; top: 338px; text-align: center;
    font-family: "Lora", serif; font-style: italic; font-weight: 600; font-size: 32px; line-height: 1.3;
    color: var(--title-brown);
  }
  .ingredient-art {
    position: absolute; left: 150px; top: 395px; width: 411px; height: 250px;
    border-radius: 140px 140px 40px 40px;
    background: radial-gradient(ellipse at 50% 70%, #f2c24a 0%, #e8a62e 35%, #8a5a8c 70%, #6a9a3a 100%);
  }
  .product-tag {
    position: absolute; left: 160px; top: 660px; width: 391px; height: 64px;
    border-radius: 32px; background: var(--brand-red);
    display: flex; align-items: center; justify-content: center;
    font-family: "Lobster", cursive; font-size: 34px; line-height: 1; color: var(--tag-text);
  }
  .net-weight {
    position: absolute; left: 0; right: 0; top: 752px; text-align: center;
    font-family: "Roboto Condensed", sans-serif; font-weight: 700; font-size: 30px; line-height: 1.2; color: var(--ink);
  }
  .accent-band {
    position: absolute; left: 0; top: 812px; width: 100%; height: 38px; background: var(--band-green);
  }
  .base {
    position: absolute; left: 0; top: 850px; width: 100%; height: 130px; background: var(--cup-white);
  }
</style>
</head>
<body>
  <div class="label">
    <div class="brand-band">
      <div class="brand-name">Velmora</div>
    </div>

    <p class="side-copy ingredients">Ingredients: Toor Dal (Lentil), Onion, Coconut, Coriander, Red Chilli, Tamarind, Salt, Turmeric, Mustard, Curry Leaves, Edible Oil, Spices. Store in a cool dry place.</p>
    <p class="side-copy usage">Microwave Safe</p>

    <h1 class="product-title">SAMBER</h1>
    <p class="product-variant">Coconut &amp; Onion Special</p>

    <div class="ingredient-art" role="img" aria-label="Coconut halves, red onions, eggplant, chayote and a heap of toor dal lentils"></div>

    <p class="product-tag">Spicy Lentil Soup</p>

    <p class="net-weight">Net Wt.: 900 Gsm (1.98 lbs)</p>
    <div class="accent-band"></div>
    <div class="base"></div>
  </div>
</body>
</html>
```